Alterations to existing business card

Here is my current logo and I want the "cafe and bar" taken off with just the words Lumo and our slogan "Savour the glow" on the card, Plus the logo.
Our Current Business Card is currently 5.5cm by 5.5cm and would like it to remain like this thanks.
The loyalty card can be 10 squares with the logo specifying the 10th coffee free. I would like the cheapest option please.
Also on our business card would like the Facebook logo and instagram Logo with TAZALUMO27 as link to our photos on instagram.

Keep Colour schemes the same please.

On the business cards

Dale Brinton Director
0427916038
dale27lumo@mailvista.test

Paula Ferrisi Principal
0428571963
paulumo@mailvista.test

Thanks Dale

Industry/Entity Type

Business

```html
<!DOCTYPE html>
<html lang="en">
<head>
<meta charset="utf-8">
<title>Lumo – Business Card and Loyalty Card</title>
<link rel="stylesheet" href="https://fonts.googleapis.com/css2?family=Open+Sans:wght@400;600;700&display=swap">
<style>
  :root {
    --gold-light: #f6cd63;
    --gold-deep: #eaae3c;
    --gold-text: #d9a23a;
    --ink: #111111;
    --paper: #ffffff;
    --stage: #e9e6e2;
    --card-size: 400px;
  }
  * { box-sizing: border-box; margin: 0; padding: 0; }
  html, body {
    width: 1200px;
    height: 900px;
    overflow: hidden;
  }
  body {
    background: var(--stage);
    font-family: "Open Sans", Arial, sans-serif;
    color: var(--ink);
    position: relative;
  }
  .card {
    position: absolute;
    top: 250px;
    width: var(--card-size);
    height: var(--card-size);
    overflow: hidden;
    box-shadow: 0 10px 30px rgba(0,0,0,0.18);
  }
  .card--front { left: 140px; }
  .card--loyalty { left: 660px; }

  /* Front card */
  .contact-band {
    background: linear-gradient(180deg, var(--gold-light), var(--gold-deep));
    position: relative;
    padding: 14px 28px 0 34px;
  }
  .contact-band--top { height: 125px; }
  .contact-band--bottom { height: 131px; padding-top: 12px; }
  .person {
    text-align: right;
    line-height: 1.15;
  }
  .person__name { font-weight: 700; font-size: 23px; }
  .person__role { font-size: 17px; }
  .contact-list {
    list-style: none;
    margin-top: 2px;
    font-size: 17px;
    line-height: 26px;
  }
  .contact-list li { display: flex; align-items: center; gap: 9px; }
  .contact-list svg { width: 14px; height: 14px; flex: none; }
  .social-links {
    position: absolute;
    right: 28px;
    bottom: 26px;
    display: flex;
    gap: 8px;
  }
  .social-links span {
    width: 24px;
    height: 24px;
    border-radius: 50%;
    border: 2px solid var(--ink);
    display: block;
  }

  .brand-band {
    height: 144px;
    background: var(--paper);
    display: flex;
    align-items: center;
    justify-content: center;
    gap: 28px;
  }
  .brand-mark {
    width: 96px;
    height: 96px;
    border-radius: 50%;
    border: 4px solid var(--gold-deep);
  }
  .brand-name {
    font-size: 38px;
    font-weight: 400;
    letter-spacing: 1px;
    line-height: 1;
  }
  .brand-slogan {
    display: block;
    font-size: 10.5px;
    color: var(--gold-text);
    letter-spacing: 1.2px;
    margin-top: 3px;
  }

  /* Loyalty card */
  .loyalty-head {
    height: 205px;
    background: var(--ink);
    display: flex;
    align-items: center;
    justify-content: center;
    gap: 22px;
  }
  .loyalty-head .brand-mark { width: 120px; height: 120px; border-width: 5px; }
  .loyalty-head .brand-name { color: var(--gold-light); font-size: 40px; }
  .stamp-area {
    height: 195px;
    background: linear-gradient(180deg, var(--gold-light), var(--gold-deep));
    padding-top: 23px;
  }
  .stamp-grid {
    display: grid;
    grid-template-columns: repeat(5, 53px);
    grid-auto-rows: 53px;
    column-gap: 12px;
    row-gap: 6px;
    justify-content: center;
  }
  .stamp {
    background: var(--ink);
    display: flex;
    align-items: center;
    justify-content: center;
  }
  .stamp span {
    width: 47px;
    height: 47px;
    border-radius: 50%;
    background: var(--paper);
    display: flex;
    align-items: center;
    justify-content: center;
    font-weight: 700;
    font-size: 24px;
  }
  .stamp--free span { font-size: 14px; }
</style>
</head>
<body>

<section class="card card--front" aria-label="Lumo business card">
  <div class="contact-band contact-band--top">
    <div class="person">
      <div class="person__name">Dale Brinton</div>
      <div class="person__role">Director</div>
    </div>
    <ul class="contact-list">
      <li>
        <svg viewBox="0 0 24 24" aria-hidden="true"><path fill="#111" d="M6.6 10.8a15.1 15.1 0 0 0 6.6 6.6l2.2-2.2c.3-.3.7-.4 1-.2 1.1.4 2.3.6 3.6.6.6 0 1 .4 1 1V20c0 .6-.4 1-1 1A17 17 0 0 1 3 4c0-.6.4-1 1-1h3.5c.6 0 1 .4 1 1 0 1.3.2 2.5.6 3.6.1.3 0 .7-.2 1z"/></svg>
        0427916038
      </li>
      <li>
        <svg viewBox="0 0 24 24" aria-hidden="true"><path fill="#111" d="M2 5h20v14H2z"/><path fill="none" stroke="#f2c25a" stroke-width="1.8" d="M2.5 6l9.5 7 9.5-7"/></svg>
        dale27lumo@mailvista.test
      </li>
    </ul>
  </div>

  <div class="brand-band">
    <div class="brand-mark" aria-hidden="true"></div>
    <div>
      <div class="brand-name">LUMO</div>
      <span class="brand-slogan">SAVOUR THE GLOW</span>
    </div>
  </div>

  <div class="contact-band contact-band--bottom">
    <div class="person">
      <div class="person__name">Paula Ferrisi</div>
      <div class="person__role">Principal</div>
    </div>
    <ul class="contact-list">
      <li>
        <svg viewBox="0 0 24 24" aria-hidden="true"><path fill="#111" d="M6.6 10.8a15.1 15.1 0 0 0 6.6 6.6l2.2-2.2c.3-.3.7-.4 1-.2 1.1.4 2.3.6 3.6.6.6 0 1 .4 1 1V20c0 .6-.4 1-1 1A17 17 0 0 1 3 4c0-.6.4-1 1-1h3.5c.6 0 1 .4 1 1 0 1.3.2 2.5.6 3.6.1.3 0 .7-.2 1z"/></svg>
        0428571963
      </li>
      <li>
        <svg viewBox="0 0 24 24" aria-hidden="true"><path fill="#111" d="M2 5h20v14H2z"/><path fill="none" stroke="#f2c25a" stroke-width="1.8" d="M2.5 6l9.5 7 9.5-7"/></svg>
        paulumo@mailvista.test
      </li>
    </ul>
    <div class="social-links" aria-label="Social media links">
      <span></span>
      <span></span>
    </div>
  </div>
</section>

<section class="card card--loyalty" aria-label="Lumo loyalty card">
  <div class="loyalty-head">
    <div class="brand-mark" aria-hidden="true"></div>
    <div class="brand-name">LUMO</div>
  </div>
  <div class="stamp-area">
    <div class="stamp-grid">
      <div class="stamp"><span>1</span></div>
      <div class="stamp"><span>2</span></div>
      <div class="stamp"><span>3</span></div>
      <div class="stamp"><span>4</span></div>
      <div class="stamp"><span>5</span></div>
      <div class="stamp"><span>6</span></div>
      <div class="stamp"><span>7</span></div>
      <div class="stamp"><span>8</span></div>
      <div class="stamp"><span>9</span></div>
      <div class="stamp stamp--free"><span>Free</span></div>
    </div>
  </div>
</section>

</body>
</html>
```